Blind Rivet Product catalogue

Need a design in wordpress with a productcatalogue where i present all products. This is a B2B business. The products is Blindrivets and Blindrivet nuts and accessories to this. I only want the basic information and also technical specification.

This is a subcompany to my existing company k7.m3.se but specializing in a subcategory

Businesses using blind rivet technology.

Industrial

Sans Serif

Must have
• Three different categories for the products; Blind Rivets - Blind Rivet Nut - Riveting Tools
Nice to have
• Possible to ad login for more information of the different sizes

```html
<!DOCTYPE html>
<html lang="en">
<head>
<meta charset="utf-8">
<title>Blind Rivet – Product Catalogue</title>
<link href="https://fonts.googleapis.com/css2?family=Roboto+Condensed:wght@400;700&family=Roboto:ital,wght@0,400;0,500;1,400&family=Poppins:wght@400;500&display=swap" rel="stylesheet">
<style>
:root{
  --black:#000;
  --orange:#ff5a00;
  --blue:#2d5fd6;
  --ink:#222;
  --grey:#666;
  --light:#ddd;
  --footer:#222;
  --white:#fff;
}
*{box-sizing:border-box;margin:0;padding:0}
html,body{width:1200px;height:2589px;overflow:hidden}
body{font-family:"Roboto",sans-serif;color:var(--ink);background:var(--white);position:relative}
.abs{position:absolute}

/* header */
.site-header{position:absolute;left:0;top:0;width:1200px;height:90px;background:var(--black)}
.brand{left:141px;top:33px;color:var(--white);font-family:"Poppins",sans-serif;font-weight:500;font-size:20px;line-height:24px;display:flex;align-items:center;gap:8px}
.brand i{display:block;width:12px;height:12px;background:var(--orange)}
.nav{left:392px;top:39px;display:flex;gap:21px;font-family:"Poppins",sans-serif;font-weight:500;font-size:14px;line-height:20px;color:var(--white)}
.nav .active{color:var(--orange)}
.login{left:859px;top:39px;font-family:"Poppins",sans-serif;font-weight:500;font-size:14px;line-height:20px;color:var(--orange);display:flex;gap:4px;align-items:center}
.cart{left:984px;top:39px;font-family:"Poppins",sans-serif;font-weight:500;font-size:14px;line-height:20px;color:var(--white);display:flex;gap:4px;align-items:center}
.cart span{color:var(--orange)}

/* hero */
.hero{left:0;top:90px;width:1200px;height:563px;background:linear-gradient(100deg,#b9b3a8 0%,#8f8a80 35%,#2f5fb0 60%,#1d3f86 100%)}
.hero-panel{left:111px;top:222px;width:494px;height:273px;background:rgba(120,120,120,.55)}
.hero-title{left:160px;top:262px;font-family:"Roboto Condensed",sans-serif;font-weight:700;font-size:52px;line-height:60px;color:var(--white)}
.hero-text{left:162px;top:323px;width:420px;font-family:"Roboto Condensed",sans-serif;font-weight:700;font-size:14px;line-height:21.5px;color:var(--white)}
.btn-blue{left:163px;top:400px;width:128px;height:43px;background:var(--blue);color:var(--white);font-family:"Roboto Condensed",sans-serif;font-weight:700;font-size:15px;display:flex;align-items:center;justify-content:center}
.hero-arrow{top:331px}

/* section headings */
.heading{width:1200px;left:0;text-align:center;font-family:"Roboto Condensed",sans-serif;font-weight:700;font-size:36px;line-height:44px}
.divider{left:525px;width:150px;height:10px}

.welcome-text{left:170px;top:826px;width:860px;text-align:center;font-size:15px;line-height:26px;color:var(--grey)}
.feature{width:160px;text-align:center;font-size:15px;color:var(--grey)}
.feature .disc{width:86px;height:86px;border-radius:50%;background:var(--light);margin:0 auto 11px;display:flex;align-items:center;justify-content:center}
.feature .disc.hot{background:var(--orange)}

/* featured */
.featured-band{left:0;top:1142px;width:1200px;height:473px;background:linear-gradient(135deg,#3a3a3a,#1e1e1e 60%,#2b2b2b)}
.card{top:1349px;width:324px;height:389px;background:var(--white)}
.card.mid{box-shadow:0 4px 14px rgba(0,0,0,.15);border:1px solid #e5e5e5}
.badge{left:11px;top:14px;width:73px;height:34px;background:var(--orange);color:var(--white);font-family:"Roboto Condensed",sans-serif;font-weight:700;font-size:14px;display:flex;align-items:center;justify-content:center}
.product-img{left:34px;top:70px;width:210px;height:116px;background:radial-gradient(ellipse at 50% 50%,#d9d9d9 0%,#eeeeee 55%,#ffffff 75%)}
.card h3{position:absolute;left:39px;top:190px;font-family:"Roboto Condensed",sans-serif;font-weight:700;font-size:23px;line-height:30px}
.card p{position:absolute;left:40px;top:224px;width:250px;font-family:"Roboto Condensed",sans-serif;font-size:15px;line-height:22px;color:#444}
.price{left:41px;top:268px;font-family:"Roboto Condensed",sans-serif;font-size:15px;line-height:26px;color:#444}
.price b{color:var(--orange);font-size:20px}
.btn-orange{left:40px;top:310px;width:129px;height:39px;background:var(--orange);color:var(--white);font-family:"Roboto Condensed",sans-serif;font-weight:700;font-size:14px;display:flex;align-items:center;justify-content:center;gap:4px}

/* testimonial */
.avatar{left:252px;top:1953px;width:145px;height:145px;border-radius:50%;background:radial-gradient(circle at 50% 60%,#c7d9e6,#6fa8d2)}
.quote-badge{left:348px;top:1946px;width:50px;height:50px;border-radius:50%;background:var(--orange);border:3px solid var(--white);color:var(--white);font-family:"Roboto Condensed",sans-serif;font-weight:700;font-size:30px;display:flex;align-items:center;justify-content:center}
.quote-text{left:432px;top:1955px;width:550px;font-style:italic;font-size:15px;line-height:26px;color:var(--grey)}
.quote-name{left:435px;top:2042px;font-size:19px;color:#444}
.quote-role{left:435px;top:2073px;font-style:italic;font-size:14px;color:var(--grey)}

/* footer */
.site-footer{left:0;top:2205px;width:1200px;height:384px;background:var(--footer)}
.ft{font-family:"Poppins",sans-serif;color:var(--white)}
.foot-brand{left:90px;width:200px;text-align:center;top:2396px;font-weight:500;font-size:23px;line-height:30px}
.foot-mark{left:168px;top:2330px;width:50px;height:50px;border-radius:50%;border:3px solid var(--white)}
.socials{left:127px;top:2435px;display:flex;gap:4px}
.socials span{width:30px;height:30px;border-radius:50%;background:var(--white);display:block}
.foot-title{top:2306px;font-weight:500;font-size:16px;line-height:22px;text-transform:uppercase}
.foot-title::after{content:"";display:block;width:78px;height:1px;background:#aaa;margin-top:7px}
.foot-list{left:380px;top:2356px;font-size:14px;line-height:28.5px}
.foot-contact{left:557px;top:2356px;font-size:14px;line-height:28.5px}
.foot-contact div{display:flex;align-items:center;gap:6px}
.sub-text{left:776px;top:2340px;width:290px;font-size:14px;line-height:28px}
.email-box{left:770px;top:2412px;width:284px;height:51px;border-radius:26px;background:var(--white);border:2px solid #ccc}
.email-box span{position:absolute;left:16px;top:15px;font-size:12px;color:#888}
.send{left:1005px;top:2414px;width:47px;height:47px;border-radius:50%;background:var(--orange);display:flex;align-items:center;justify-content:center}
.copy{top:2532px;font-size:14px}
</style>
</head>
<body>

<header class="site-header">
  <div class="abs brand"><i></i>K7M3</div>
  <nav class="abs nav"><span class="active">HOME</span><span>ABOUT US</span><span>PRODUCT</span><span>REVIEWS</span><span>CONTACT US</span></nav>
  <div class="abs login"><svg width="15" height="15" viewBox="0 0 16 16"><circle cx="8" cy="8" r="7" fill="none" stroke="#ff5a00" stroke-width="1.6"/><circle cx="8" cy="6" r="2.5" fill="#ff5a00"/><path d="M3.5 12.5c1.5-2.5 7.5-2.5 9 0" fill="#ff5a00"/></svg>LOGIN</div>
  <div class="abs cart"><svg width="16" height="14" viewBox="0 0 16 14"><path d="M0 1h3l2 8h9l2-6H4" fill="none" stroke="#fff" stroke-width="1.8"/><circle cx="6" cy="12" r="1.5" fill="#fff"/><circle cx="13" cy="12" r="1.5" fill="#fff"/></svg>CART <span>$ 0.00</span></div>
</header>

<section>
  <div class="abs hero" role="img" aria-label="Worker in blue overalls operating a riveting tool in a workshop"></div>
  <div class="abs hero-panel"></div>
  <h1 class="abs hero-title">BLIND RIVET</h1>
  <p class="abs hero-text">LOREM IPSUM DOLOR SIT AMET, CONSECTETUR ADIPISCING ELIT,<br>SED DO EIUSMOD TEMPOR INCIDIDUNT UT LABORE ET DOLORE<br>MAGNA ALIQUA.</p>
  <div class="abs btn-blue">GET STARTED</div>
  <svg class="abs hero-arrow" style="left:42px" width="22" height="34" viewBox="0 0 22 34"><path d="M17 3L5 17l12 14" fill="none" stroke="#444" stroke-width="3"/></svg>
  <svg class="abs hero-arrow" style="left:1136px" width="22" height="34" viewBox="0 0 22 34"><path d="M5 3l12 14L5 31" fill="none" stroke="#ccc" stroke-width="3"/></svg>
</section>

<section>
  <h2 class="abs heading" style="top:758px">WELCOME</h2>
  <svg class="abs divider" style="top:800px" viewBox="0 0 150 10"><line x1="0" y1="5" x2="64" y2="5" stroke="#222" stroke-width="2"/><circle cx="75" cy="5" r="4.5" fill="#ff5a00"/><line x1="86" y1="5" x2="150" y2="5" stroke="#222" stroke-width="2"/></svg>
  <p class="abs welcome-text">Lorem ipsum dolor sit amet, consectetur adipiscing elit, sed do eiusmod tempor incididunt ut labore et dolore magna aliqua. Ut enim ad minim veniam, quis nostrud exercitation ullamco laboris nisi ut aliquip ex ea commodo consequat. Duis aute irure dolor in reprehenderit in voluptate velit esse cillum dolore eu fugiat nulla pariatur.</p>
  <div class="abs feature" style="left:293px;top:929px"><div class="disc"><svg width="40" height="40" viewBox="0 0 40 40" fill="none" stroke="#333" stroke-width="1.6"><circle cx="20" cy="20" r="9"/><circle cx="20" cy="20" r="4"/><path d="M20 6v5M20 29v5M6 20h5M29 20h5M10 10l4 4M26 26l4 4M30 10l-4 4M14 26l-4 4"/></svg></div>Lorem ipsum dolor</div>
  <div class="abs feature" style="left:520px;top:929px"><div class="disc hot"><svg width="40" height="40" viewBox="0 0 40 40" fill="none" stroke="#fff" stroke-width="1.6"><rect x="7" y="18" width="26" height="14"/><path d="M10 18v-6h6v6M22 18V8h6v10M10 24h20M10 28h20"/></svg></div>Lorem ipsum dolor</div>
  <div class="abs feature" style="left:747px;top:929px"><div class="disc"><svg width="40" height="40" viewBox="0 0 40 40" fill="none" stroke="#333" stroke-width="1.6"><circle cx="20" cy="16" r="10"/><circle cx="20" cy="16" r="6"/><path d="M14 24l-4 10 5-2 3 4 2-8M26 24l4 10-5-2-3 4-2-8"/></svg></div>Lorem ipsum dolor</div>
</section>

<section>
  <div class="abs featured-band" role="img" aria-label="Dark workshop background with riveting tools"></div>
  <h2 class="abs heading" style="top:1248px;color:var(--white)">OUR FEATURED PRODUCT</h2>
  <svg class="abs divider" style="top:1297px" viewBox="0 0 150 10"><line x1="0" y1="5" x2="64" y2="5" stroke="#fff" stroke-width="2"/><circle cx="75" cy="5" r="4.5" fill="#ff5a00"/><line x1="86" y1="5" x2="150" y2="5" stroke="#fff" stroke-width="2"/></svg>

  <article class="abs card" style="left:113px">
    <div class="abs badge">NEW</div>
    <div class="abs product-img" role="img" aria-label="Blind rivet product photo"></div>
    <h3>Blind Rivets</h3>
    <p>Lorem ipsum dolor sit amet, consectetur adipiscing Lorem ipsum dolor</p>
    <div class="abs price">Price : <b>$ 50.00</b></div>
    <div class="abs btn-orange">LEARN MORE <svg width="13" height="13" viewBox="0 0 14 14"><circle cx="7" cy="7" r="6.5" fill="#fff"/><path d="M5 4l3 3-3 3" fill="none" stroke="#ff5a00" stroke-width="2"/></svg></div>
  </article>
  <article class="abs card mid" style="left:437px">
    <div class="abs badge">NEW</div>
    <div class="abs product-img" role="img" aria-label="Blind rivet nut product photo"></div>
    <h3>Blind Rivet Nut</h3>
    <p>Lorem ipsum dolor sit amet, consectetur adipiscing Lorem ipsum dolor</p>
    <div class="abs price">Price : <b>$ 50.00</b></div>
    <div class="abs btn-orange">LEARN MORE <svg width="13" height="13" viewBox="0 0 14 14"><circle cx="7" cy="7" r="6.5" fill="#fff"/><path d="M5 4l3 3-3 3" fill="none" stroke="#ff5a00" stroke-width="2"/></svg></div>
  </article>
  <article class="abs card" style="left:761px">
    <div class="abs badge">NEW</div>
    <div class="abs product-img" role="img" aria-label="Cordless riveting tool product photo"></div>
    <h3>Riveting Tools</h3>
    <p>Lorem ipsum dolor sit amet, consectetur adipiscing Lorem ipsum dolor</p>
    <div class="abs price">Price : <b>$ 50.00</b></div>
    <div class="abs btn-orange">LEARN MORE <svg width="13" height="13" viewBox="0 0 14 14"><circle cx="7" cy="7" r="6.5" fill="#fff"/><path d="M5 4l3 3-3 3" fill="none" stroke="#ff5a00" stroke-width="2"/></svg></div>
  </article>
</section>

<section>
  <h2 class="abs heading" style="top:1846px">WHAT OUR CLIENT SAYS</h2>
  <svg class="abs divider" style="top:1896px" viewBox="0 0 150 10"><line x1="0" y1="5" x2="64" y2="5" stroke="#222" stroke-width="2"/><circle cx="75" cy="5" r="4.5" fill="#ff5a00"/><line x1="86" y1="5" x2="150" y2="5" stroke="#222" stroke-width="2"/></svg>
  <svg class="abs" style="left:86px;top:2004px" width="46" height="30" viewBox="0 0 46 30"><path d="M44 15H3M16 2L3 15l13 13" fill="none" stroke="#999" stroke-width="2.5"/></svg>
  <svg class="abs" style="left:1066px;top:2004px" width="46" height="30" viewBox="0 0 46 30"><path d="M2 15h41M30 2l13 13-13 13" fill="none" stroke="#999" stroke-width="2.5"/></svg>
  <div class="abs avatar" role="img" aria-label="Portrait of client John Doe"></div>
  <div class="abs quote-badge">“</div>
  <p class="abs quote-text">Lorem ipsum dolor sit amet, consectetur adipiscing elit, sed do eiusmod tempor incididunt ut labore et dolore magna aliqua. Ut enim ad minim veniam, quis nostrud exercitation ullamco laboris nisi ut aliquip ex ea commodo consequat.</p>
  <div class="abs quote-name">John Doe</div>
  <div class="abs quote-role">CEO, Company Name</div>
</section>

<footer class="abs site-footer"></footer>
<div class="abs foot-mark"></div>
<div class="abs ft foot-brand">BLIND RIVET</div>
<div class="abs socials"><span></span><span></span><span></span><span></span></div>

<div class="abs ft foot-title" style="left:378px">Quick Links</div>
<div class="abs ft foot-list">Home<br>About us<br>Product<br>Reviews<br>Contact us</div>

<div class="abs ft foot-title" style="left:562px">Contact Us</div>
<div class="abs ft foot-contact">
  <div><svg width="12" height="12" viewBox="0 0 12 12"><path d="M2 1l2 0 1 3-1.5 1a7 7 0 0 0 3.5 3.5L8 7l3 1v2a1 1 0 0 1-1 1C5 11 1 7 1 2a1 1 0 0 1 1-1z" fill="#fff"/></svg>888-888-8888</div>
  <div><svg width="13" height="11" viewBox="0 0 13 11"><rect x="1" y="1" width="11" height="9" fill="none" stroke="#fff" stroke-width="1.3"/><path d="M1 1l5.5 5L12 1" fill="none" stroke="#fff" stroke-width="1.3"/></svg>info@rivetcatalog.example</div>
  <div><svg width="10" height="13" viewBox="0 0 10 13"><path d="M5 0a5 5 0 0 1 5 5c0 3-5 8-5 8S0 8 0 5a5 5 0 0 1 5-5z" fill="#fff"/><circle cx="5" cy="5" r="1.8" fill="#222"/></svg>1234 location sed lomer</div>
  <div style="padding-left:14px">sed xxxx NY xxxx</div>
</div>

<div class="abs ft foot-title" style="left:776px">Subscribe to our blog</div>
<p class="abs ft sub-text">Sign up today to get resources on how to attract and retain more customers!</p>
<div class="abs email-box"><span style="font-family:'Poppins',sans-serif">Email Address</span></div>
<div class="abs send"><svg width="20" height="20" viewBox="0 0 20 20"><path d="M18 2L2 9l6 2 2 7z" fill="#fff"/></svg></div>

<div class="abs ft copy" style="left:79px">Copyright © 2020. All Rights Reserved</div>
<div class="abs ft copy" style="left:801px">Terms and Conditions | Privacy Policy</div>

</body>
</html>
```